Call Center In Need of Website Design

We are a call center that provides inbound and outbound calling & marketing services for eCommerce store. We would like to see a fun, creative, playful design that is simple.

Here are some sample design sites we like;
- https://www.velmoreline.com/
- https://pindrask.io/
- https://www.glimbertic.com/live-chat-software/
- https://www.zavrolin.com/

Here are some competitor sites;
- https://www.ostrevaglinks.com/
- https://www.helpkestrel.com/

I have attached website content for your use.

Target Market(s)

eCommerce

Coding

Coded - Design and coding required

Number of Pages Required

5+ page

Font styles to use
Sans Serif

Colors

Designer to choose colors to be used in the design.

Requirements
Must have
• Must have designs for the following 5 separate pages;
• 1. Home (landing)
• - This will be were the design style really needs to show.
• - Just needs to touch on key services
• - CTA
• 2. About Us
• - Basic page for about me paragraph
• 3. Services
• - List of services with icons
• - Click on service type to expand details or hover over service icon to view popup bubble with details about that service
• 4. Pricing
• - Option to bundle 1(one) digital service plan and 1(one) call center service plan
• - Bundling adds 10% monthly discount to over all price
• - Customer does NOT have to bundle
• - FAQ
• 5. Contact Us
• - Include a capture form (name, company name, email, phone, message)
• - Contact info
• - Business hours
• When customer purchases their desired plan, then they are taken to a page where they must schedule a call with an account rep.
Nice to have
• home page animations
Should not have
• All information on Home/Landing page.

```html
<!DOCTYPE html>
<html lang="en">
<head>
<meta charset="utf-8">
<title>Orbitra — Omnichannel Customer Care</title>
<link rel="stylesheet" href="https://fonts.googleapis.com/css2?family=Exo+2:wght@300;400;500;600;700&display=swap">
<style>
:root{
  --teal-hero:#2ec9b4;
  --teal:#1dbba6;
  --teal-tile:#20bca6;
  --ink:#1b1b1b;
  --grey-text:#7a7a7a;
  --grey-head:#6f6f6f;
  --grey-band:#eeeeee;
  --footer:#0e0e0e;
  --white:#ffffff;
}
*{margin:0;padding:0;box-sizing:border-box}
html,body{width:730px;height:1200px;overflow:hidden;background:var(--white)}
body{position:relative;font-family:"Exo 2",sans-serif;color:var(--ink)}
.abs{position:absolute}

/* Hero */
.hero{left:0;top:0;width:730px;height:408px;background:var(--teal-hero);overflow:hidden}
.brand{left:98px;top:22px;display:flex;align-items:center;gap:12px}
.brand-dot{width:38px;height:38px;border-radius:50%;border:3px solid var(--white)}
.brand-name{font-size:26px;font-weight:400;letter-spacing:4px;color:#4d5b5b}
.nav-link{top:36px;font-size:5.5px;font-weight:700;color:var(--white);letter-spacing:.3px}
.nav-link.hamburger{left:543px;text-decoration:underline}
.nav-link.menu{left:603px;display:flex;align-items:center;gap:5px}
.menu-icon{width:10px;height:7px;border-top:1px solid #fff;border-bottom:1px solid #fff;position:relative}
.menu-icon::after{content:"";position:absolute;left:0;right:0;top:2px;border-top:1px solid #fff}
.hero-title{left:95px;top:100px;font-size:27.5px;line-height:31px;font-weight:500;color:var(--white);letter-spacing:-.2px}
.cta{left:98px;top:184px;width:83px;height:25px;border-radius:13px;background:var(--white);font-size:7px;font-weight:600;display:flex;align-items:center;justify-content:center;color:var(--ink)}
.hero-copy{left:98px;top:222px;width:400px;font-size:8px;line-height:12.5px;color:#173a36}
.arrow{top:198px}
.arrow.prev{left:26px}
.arrow.next{left:682px}
.hero-art{left:150px;top:252px;width:446px;height:156px;background:linear-gradient(180deg,#5fd8c8 0%,#3fd0bd 60%,#7fe6da 100%);border-radius:6px 6px 0 0}

/* What we do */
.about-title{left:98px;top:462px;font-size:28px;font-weight:400;color:var(--grey-head)}
.about-title strong{color:var(--teal);font-weight:600}
.about-copy{left:98px;top:504px;width:350px;font-size:7px;line-height:12.6px;color:var(--grey-text)}
.about-art{left:468px;top:446px;width:150px;height:104px;background:linear-gradient(180deg,#f3f3f3,#e4e4e4);border-radius:6px}

/* Services */
.services{left:0;top:606px;width:730px;height:224px;background:var(--grey-band)}
.notch{left:350px;top:0;width:30px;height:26px}
.section-title{left:0;width:730px;text-align:center;font-size:8.5px;font-weight:700;letter-spacing:1.1px}
.services .section-title{top:33px;color:var(--ink)}
.plan{top:61px;width:207px;height:124px;border:1px dashed #b9b9b9}
.plan.digital{left:127px}
.plan.call{left:396px}
.plan-link{left:334px;top:122px;width:62px;border-top:1px dashed #b9b9b9}
.tile{position:absolute;width:58px;height:28px;background:var(--teal-tile);border-radius:3px;color:var(--white);font-size:5px;font-weight:700;line-height:6.5px;text-transform:uppercase;display:flex;align-items:center;justify-content:center;text-align:center;box-shadow:0 1px 2px rgba(0,0,0,.12)}
.tile.feature{height:51px;background:#0b0b0b;font-size:8.5px;font-weight:400;line-height:10px;text-transform:none}
.c1{left:14px}.c2{left:75px}.c3{left:136px}
.r1{top:14px}.r2{top:47px}.r3{top:81px}

/* FAQ */
.faq{left:0;top:830px;width:730px;height:173px;background:var(--teal)}
.faq-rule{left:365px;top:0;width:1px;height:52px;background:rgba(255,255,255,.45)}
.faq .section-title{top:48px;color:var(--white)}
.faq-answer{left:100px;top:71px;width:530px;text-align:center;font-size:8.5px;line-height:13.5px;color:var(--white)}
.faq-question{left:0;top:111px;width:730px;text-align:center;font-size:8px;font-weight:600;color:var(--ink)}
.pager{top:131px;width:16px;height:16px;border-radius:2px;display:flex;align-items:center;justify-content:center}
.pager.prev{left:346px;background:#138f7f}
.pager.next{left:367px;border:1px solid var(--white)}

/* Footer */
.footer{left:0;top:1003px;width:730px;height:197px;background:var(--footer);color:var(--white)}
.foot-head{top:20px;font-size:5.5px;font-weight:700;letter-spacing:.2px}
.foot-list{top:34px;list-style:none;font-size:6px;line-height:12.8px}
.foot-list.social a{color:var(--white);text-decoration:underline;display:block;line-height:16.5px}
.col1{left:98px}.col2{left:262px}.col3{left:420px}
.foot-brand{left:420px;top:33px;display:flex;align-items:center;gap:12px}
.foot-brand .brand-dot{width:36px;height:36px;border-color:#6fe0c8}
.foot-brand .brand-name{font-size:23px;color:#6d6d6d}
.foot-address{left:420px;top:83px;font-size:6px;line-height:9.5px}
.foot-phone{left:420px;top:107px;font-size:6px;display:flex;align-items:center;gap:6px}
.foot-rule{left:98px;top:162px;width:534px;border-top:1px solid #333}
.copyright{left:98px;top:177px;font-size:5.5px}
</style>
</head>
<body>

<header class="hero abs">
  <div class="brand abs"><span class="brand-dot"></span><span class="brand-name">ORBITRA</span></div>
  <span class="nav-link hamburger abs">HAMBURGER</span>
  <span class="nav-link menu abs">MENU <span class="menu-icon"></span></span>

  <h1 class="hero-title abs">ORBITRA IS AN OMNICHANNEL<br>PROVIDER FOR CUSTOMER CARE</h1>
  <a class="cta abs">GET STARTED</a>
  <p class="hero-copy abs">We are a call center that provides inbound and outbound calling &amp; marketing services for eCommerce store. We would like to see a fun, creative, playful design that is simple.</p>

  <svg class="arrow prev abs" width="20" height="8" viewBox="0 0 20 8"><path d="M20 4H1M4 1L1 4l3 3" stroke="#fff" stroke-width="1" fill="none"/></svg>
  <svg class="arrow next abs" width="20" height="8" viewBox="0 0 20 8"><path d="M0 4h19M16 1l3 3-3 3" stroke="#fff" stroke-width="1" fill="none"/></svg>

  <div class="hero-art abs" role="img" aria-label="Line illustration of a customer care team with headsets working at laptops, surrounded by support icons"></div>
</header>

<section class="what">
  <h2 class="about-title abs">What <strong>Orbitra</strong> Do</h2>
  <p class="about-copy abs">Orbitra is your personal customer service &amp; product research team. We love eCommerce, but we love seeing business owners succeed even more! That is exactly why we have developed the processes &amp; technology to take care of the most over looked areas in eCommerce - Customer Service &amp; Retention.</p>
  <div class="about-art abs" role="img" aria-label="Line drawing of a headset with 24/7 support label"></div>
</section>

<section class="services abs">
  <svg class="notch abs" viewBox="0 0 30 26"><path d="M0 0Q15 0 15 26Q15 0 30 0Z" fill="#fff"/><path d="M15 8V26" stroke="#cfcfcf" stroke-width="1"/></svg>
  <h3 class="section-title abs">ORBITRA SERVICES</h3>

  <div class="plan digital abs">
    <div class="tile c1 r1">Email Support</div>
    <div class="tile feature c2 r1">Digital<br>Services</div>
    <div class="tile c3 r1">Product<br>Listing</div>
    <div class="tile c1 r2">Live Chat<br>Support</div>
    <div class="tile c3 r2">Price<br>Monitoring</div>
    <div class="tile c1 r3">Product<br>Research</div>
    <div class="tile c2 r3">Click Here</div>
    <div class="tile c3 r3">Product Photo<br>&amp; Video Editing</div>
  </div>
  <div class="plan-link abs"></div>
  <div class="plan call abs">
    <div class="tile c1 r1">Email Support</div>
    <div class="tile feature c2 r1">Call Center<br>Services</div>
    <div class="tile c3 r1">Product<br>Listing</div>
    <div class="tile c1 r2">Live Chat<br>Support</div>
    <div class="tile c3 r2">Price<br>Monitoring</div>
    <div class="tile c1 r3">Product<br>Research</div>
    <div class="tile c2 r3">Click Here</div>
    <div class="tile c3 r3">Product Photo<br>&amp; Video Editing</div>
  </div>
</section>

<section class="faq abs">
  <svg class="notch abs" viewBox="0 0 30 26"><path d="M0 0Q15 0 15 26Q15 0 30 0Z" fill="#eeeeee"/></svg>
  <div class="faq-rule abs"></div>
  <h3 class="section-title abs">FREQUENTLY ASKED QUESTIONS</h3>
  <p class="faq-answer abs">The free trial only relates to the "call center" service packages! There is no hidden fine print or fees to get started. We don't even require any payment info, signatures, or deposits. If you don't like us or our service, just simply walk away.</p>
  <p class="faq-question abs">Is the free trial really free?</p>
  <span class="pager prev abs"><svg width="6" height="6" viewBox="0 0 6 6"><path d="M5 0v6L1 3z" fill="#fff"/></svg></span>
  <span class="pager next abs"><svg width="6" height="6" viewBox="0 0 6 6"><path d="M1 0v6l4-3z" fill="#fff"/></svg></span>
</section>

<footer class="footer abs">
  <h4 class="foot-head col1 abs">NAVIGATIONS</h4>
  <ul class="foot-list col1 abs">
    <li>- Home</li><li>- About</li><li>- Service</li><li>- Blogs</li><li>- Events</li><li>- Contact Us</li>
  </ul>
  <h4 class="foot-head col2 abs">FOLLOW US</h4>
  <div class="foot-list social col2 abs"><a>Loopsocial</a><a>Chatterly</a></div>
  <h4 class="foot-head col3 abs">ABOUT</h4>
  <div class="foot-brand abs"><span class="brand-dot"></span><span class="brand-name">ORBITRA</span></div>
  <p class="foot-address abs">Orbitra, Inc.<br>418 Alder Crest Ave. Marlow, CA 90417</p>
  <p class="foot-phone abs"><svg width="7" height="12" viewBox="0 0 7 12"><rect x=".5" y=".5" width="6" height="11" rx="1" fill="none" stroke="#fff"/><path d="M2.5 10h2" stroke="#fff"/></svg>(555) 014-0152</p>
  <div class="foot-rule abs"></div>
  <p class="copyright abs">© Copyright 2018 Orbitra. All Rights Reserved.</p>
</footer>

</body>
</html>
```